MRT Property - Business Cards

Looking for a business card & general letterhead, signage etc design for our new logo.

Colours:
000a20
0056a2
00b5ef
0088ce
68cef2

Fonts:
Poppins
Karla

Please keep look and feel of new brand - example in the zip package I sent.

```html
<!DOCTYPE html>
<html lang="en">
<head>
<meta charset="utf-8">
<title>MRT Property – Stationery</title>
<link href="https://fonts.googleapis.com/css2?family=Poppins:wght@400;600;700&display=swap" rel="stylesheet">
<style>
  :root{
    --ink:#000a20;
    --navy:#0056a2;
    --sky:#00b5ef;
    --blue:#0088ce;
    --light:#68cef2;
    --envelope:#1ea6d8;
    --paper:#ffffff;
    --stage:#d9d9d9;
  }
  *{box-sizing:border-box;margin:0;padding:0}
  html,body{width:1200px;height:686px;overflow:hidden}
  body{background:var(--stage);font-family:"Poppins",sans-serif;color:var(--ink);position:relative}

  .sheet{position:absolute;background:var(--paper);box-shadow:0 6px 18px rgba(0,0,0,.18);overflow:hidden}
  .corners{position:absolute;inset:0;width:100%;height:100%}

  /* Letterhead */
  .letterhead{left:60px;top:40px;width:430px;height:606px}
  .letterhead .brand{position:absolute;top:44px;right:44px;display:flex;align-items:center;gap:8px;
    font-weight:700;font-size:22px;color:var(--navy);letter-spacing:.5px}
  .brand .dot{width:14px;height:14px;border-radius:50%;background:var(--sky)}
  .letterhead .watermark{position:absolute;top:250px;left:0;right:0;text-align:center;
    font-weight:700;font-size:52px;color:#eef3fa}
  .contact{position:absolute;list-style:none;text-align:right;color:var(--ink)}
  .contact li{display:flex;justify-content:flex-end;align-items:center;gap:6px}
  .contact svg{fill:var(--blue);flex:none}
  .letterhead .contact{right:44px;bottom:48px;font-size:10.5px;line-height:17px}
  .letterhead .contact svg{width:11px;height:11px}

  /* Business card */
  .card{left:640px;top:52px;width:420px;height:240px}
  .card .brand{position:absolute;top:38px;right:34px;display:flex;align-items:center;gap:7px;
    font-weight:700;font-size:19px;color:var(--navy)}
  .card .brand .dot{width:12px;height:12px}
  .card .contact{right:34px;bottom:30px;font-size:9px;line-height:14px}
  .card .contact svg{width:9px;height:9px}

  /* Envelope */
  .envelope{left:600px;top:350px;width:520px;height:270px;background:var(--envelope)}
  .envelope .flap{position:absolute;inset:0;width:100%;height:100%}
  .envelope .name{position:absolute;left:0;right:0;top:118px;text-align:center;
    font-weight:600;font-size:16px;color:var(--paper)}
</style>
</head>
<body>

<svg width="0" height="0" style="position:absolute">
  <defs>
    <symbol id="icon-phone" viewBox="0 0 24 24"><path d="M6.6 10.8a15 15 0 0 0 6.6 6.6l2.2-2.2a1 1 0 0 1 1-.25 11.4 11.4 0 0 0 3.6.57 1 1 0 0 1 1 1V20a1 1 0 0 1-1 1A17 17 0 0 1 3 4a1 1 0 0 1 1-1h3.5a1 1 0 0 1 1 1c0 1.25.2 2.45.57 3.57a1 1 0 0 1-.25 1z"/></symbol>
    <symbol id="icon-globe" viewBox="0 0 24 24"><path d="M12 2a10 10 0 1 0 0 20 10 10 0 0 0 0-20zm6.9 6h-3a15.6 15.6 0 0 0-1.4-3.6A8 8 0 0 1 18.9 8zM12 4c.8 1.2 1.5 2.5 1.9 4h-3.8c.4-1.5 1.1-2.8 1.9-4zM4.3 14a8.2 8.2 0 0 1 0-4h3.4a16.5 16.5 0 0 0 0 4zm.8 2h3a15.6 15.6 0 0 0 1.4 3.6A8 8 0 0 1 5.1 16zm3-8h-3a8 8 0 0 1 4.3-3.6C8.9 5.5 8.4 6.7 8.1 8zM12 20c-.8-1.2-1.5-2.5-1.9-4h3.8c-.4 1.5-1.1 2.8-1.9 4zm2.3-6H9.7a14.7 14.7 0 0 1 0-4h4.6a14.7 14.7 0 0 1 0 4zm.3 5.6c.6-1.1 1.1-2.3 1.4-3.6h3a8 8 0 0 1-4.4 3.6zm1.7-5.6a16.5 16.5 0 0 0 0-4h3.4a8.2 8.2 0 0 1 0 4z"/></symbol>
    <symbol id="icon-mail" viewBox="0 0 24 24"><path d="M3 5h18a1 1 0 0 1 1 1v12a1 1 0 0 1-1 1H3a1 1 0 0 1-1-1V6a1 1 0 0 1 1-1zm9 7.5L4 7.3V17h16V7.3z"/></symbol>
    <symbol id="icon-pin" viewBox="0 0 24 24"><path d="M12 2a7 7 0 0 0-7 7c0 5.2 7 13 7 13s7-7.8 7-13a7 7 0 0 0-7-7zm0 9.5A2.5 2.5 0 1 1 12 6.5a2.5 2.5 0 0 1 0 5z"/></symbol>
  </defs>
</svg>

<section class="sheet letterhead">
  <svg class="corners" viewBox="0 0 430 606" preserveAspectRatio="none" aria-hidden="true">
    <polygon points="0,0 190,0 190,10 22,10 0,70" fill="var(--light)"/>
    <polygon points="0,0 70,0 22,10 0,70" fill="var(--blue)"/>
    <polygon points="0,420 10,440 10,606 0,606" fill="var(--light)"/>
    <polygon points="0,560 10,560 40,606 0,606" fill="var(--blue)"/>
    <polygon points="430,0 430,200 420,200 420,40" fill="var(--blue)"/>
    <polygon points="430,190 430,290 420,290 420,200" fill="var(--light)"/>
    <polygon points="430,470 430,606 250,606 250,596 420,596" fill="var(--blue)"/>
  </svg>
  <div class="brand"><span class="dot"></span>MRT Property</div>
  <div class="watermark">MRT Property</div>
  <ul class="contact">
    <li>+61 2 5550 1234 <svg><use href="#icon-phone"/></svg></li>
    <li>www.mrtproperty.com.au <svg><use href="#icon-globe"/></svg></li>
    <li>info@mrtproperty.com.au <svg><use href="#icon-mail"/></svg></li>
    <li>Suite 104, Block 3 <svg><use href="#icon-pin"/></svg></li>
    <li>18 Harbourline Road, Westbrook,</li>
    <li>Westbrook NSW 2150</li>
  </ul>
</section>

<section class="sheet card">
  <svg class="corners" viewBox="0 0 420 240" preserveAspectRatio="none" aria-hidden="true">
    <polygon points="0,0 130,0 130,8 16,8 0,40" fill="var(--light)"/>
    <polygon points="0,0 50,0 16,8 0,40" fill="var(--blue)"/>
    <polygon points="420,240 420,150 412,150 412,226 300,232 300,240" fill="var(--light)"/>
    <polygon points="420,240 420,200 412,226 370,240" fill="var(--blue)"/>
  </svg>
  <div class="brand"><span class="dot"></span>MRT Property</div>
  <ul class="contact">
    <li>+61 2 5550 1234 <svg><use href="#icon-phone"/></svg></li>
    <li>www.mrtproperty.com.au <svg><use href="#icon-globe"/></svg></li>
    <li>info@mrtproperty.com.au <svg><use href="#icon-mail"/></svg></li>
    <li>Suite 104, Block 3 <svg><use href="#icon-pin"/></svg></li>
    <li>18 Harbourline Road, Westbrook,</li>
    <li>Westbrook NSW 2150</li>
  </ul>
</section>

<section class="sheet envelope">
  <svg class="flap" viewBox="0 0 520 270" preserveAspectRatio="none" aria-hidden="true">
    <polygon points="0,0 520,0 520,30 300,150 220,150 0,30" fill="#22ade0"/>
    <polyline points="0,30 220,150 300,150 520,30" fill="none" stroke="#1890c2" stroke-width="2"/>
  </svg>
  <div class="name">MRT Property</div>
</section>

</body>
</html>
```